mechanical repair shop

our shop repairs light and medium duty trucks

we sell tires , do oil changes, engine and transmissions
vehicle accessories, alignments, brakes , exhaust, all major and minor repairs.
Updates

if you would like to get a hold of me email: milo.hensworth@quarrytide.net tel: 1-780-555-0148

Target Market(s)

light and medium duty trucks and cars

Industry/Entity Type

Shop

Colors
f37122

Requirements
Must have
• visual sales displays
Nice to have
• pictures

```html
<!DOCTYPE html>
<html lang="en">
<head>
<meta charset="utf-8">
<title>Quarrytide Production Services – Truck Repair Flyer</title>
<link href="https://fonts.googleapis.com/css2?family=Oswald:wght@300;400;600;700&family=Montserrat:ital,wght@0,400;0,500;1,400&display=swap" rel="stylesheet">
<style>
  :root{
    --orange:#f37122;
    --black:#000000;
    --white:#ffffff;
    --ink:#1c1c1c;
    --stage:#e9e9e9;
  }
  *{box-sizing:border-box;margin:0;padding:0}
  html,body{width:960px;height:1200px;overflow:hidden;background:var(--stage)}
  .flyer{position:absolute;left:56px;top:0;width:848px;height:1200px;background:var(--black);overflow:hidden}
  .flyer__shapes{position:absolute;inset:0}
  .photo{position:absolute}
  .photo--trucks{left:0;top:128px;width:650px;height:245px;
    background:linear-gradient(180deg,#f4f4f4 0%,#dcdcdc 55%,#3a3a3a 88%,#000 100%)}
  .photo--round{border-radius:50%;border:14px solid var(--orange)}
  .photo--tire{left:38px;top:375px;width:310px;height:310px;
    background:radial-gradient(circle at 55% 55%,#2a2a2a 0%,#555 45%,#9a9a9a 75%,#c9c9c9 100%)}
  .photo--oil{left:234px;top:988px;width:192px;height:192px;border-width:10px;
    background:radial-gradient(circle at 55% 45%,#d9a520 0%,#7a6a4a 35%,#4a4a4a 65%,#9a9a9a 100%)}
  .brand{position:absolute;left:612px;top:20px;width:212px;height:166px;border-radius:50%;
    background:var(--black);border:3px solid var(--orange);display:flex;flex-direction:column;
    align-items:center;justify-content:center;gap:2px}
  .brand__name{font-family:"Oswald",sans-serif;font-weight:700;font-size:26px;color:var(--orange);letter-spacing:1px;text-transform:uppercase}
  .brand__sub{font-family:"Oswald",sans-serif;font-weight:700;font-size:11px;color:var(--orange);letter-spacing:1px}
  .headline{position:absolute;left:390px;top:370px;width:440px;font-family:"Oswald",sans-serif;font-weight:600;
    font-size:29px;line-height:40px;color:var(--white);text-transform:uppercase;letter-spacing:-0.8px;white-space:nowrap}
  .headline__line{display:block}
  .headline__line--second{padding-left:4px}
  .headline .accent{color:var(--orange)}
  .services{position:absolute;left:440px;top:536px;width:400px}
  .services__title{font-family:"Oswald",sans-serif;font-weight:400;font-size:38px;color:var(--orange);line-height:1;margin-bottom:16px}
  .services__list{list-style:none}
  .services__item{display:flex;align-items:center;gap:10px;font-family:"Montserrat",sans-serif;
    font-size:15px;color:var(--ink);height:32.8px}
  .services__item svg{flex:none}
  .about{position:absolute;left:30px;top:713px;width:353px;font-family:"Montserrat",sans-serif;
    font-style:italic;font-size:13px;line-height:24.1px;color:var(--ink);text-align:justify}
  .website{position:absolute;left:38px;top:1146px;font-family:"Oswald",sans-serif;font-weight:300;font-size:22px;color:var(--white)}
  .contact{position:absolute;right:40px;top:1088px;text-align:right}
  .contact__label{font-family:"Oswald",sans-serif;font-weight:400;font-size:24px;color:var(--orange)}
  .contact__phone{display:flex;align-items:center;justify-content:flex-end;gap:8px;
    font-family:"Oswald",sans-serif;font-weight:300;font-size:46px;color:var(--white);line-height:1.1}
</style>
</head>
<body>
<main class="flyer">
  <svg class="flyer__shapes" width="848" height="1200" viewBox="0 0 848 1200" aria-hidden="true">
    <path d="M338,0 L848,0 L848,232 C700,285 490,265 390,185 C340,140 320,70 338,0 Z" fill="var(--white)"/>
    <path d="M612,322 C720,292 790,262 848,232 L848,258 C790,284 720,308 612,322 Z" fill="var(--orange)"/>
    <path d="M345,474 C450,476 560,486 622,500 C540,492 440,486 345,484 Z" fill="var(--orange)"/>
    <path d="M0,606 C180,520 560,515 848,535 L848,1012 C600,1062 300,1088 0,1088 Z" fill="var(--white)"/>
    <path d="M0,606 C8,572 26,546 52,524 L58,540 C32,560 12,590 4,612 Z" fill="var(--orange)"/>
    <path d="M0,1018 C120,1028 200,1058 250,1108 C180,1100 80,1094 0,1092 Z" fill="var(--orange)"/>
  </svg>

  <div class="photo photo--trucks" role="img" aria-label="Photo of three white light and medium duty box trucks"></div>

  <div class="brand">
    <span class="brand__name">Quarrytide</span>
    <span class="brand__sub">Production Services Ltd.</span>
  </div>

  <h1 class="headline">
    <span class="headline__line">Your complete <span class="accent">light medium duty</span></span>
    <span class="headline__line headline__line--second"><span class="accent">truck</span> repair facility</span>
  </h1>

  <div class="photo photo--round photo--tire" role="img" aria-label="Photo of a mechanic mounting a tire on a tire changer"></div>

  <section class="services">
    <h2 class="services__title">Services We Offer:</h2>
    <ul class="services__list">
      <li class="services__item"><svg width="14" height="14" viewBox="0 0 14 14"><circle cx="7" cy="7" r="5.8" fill="none" stroke="#f37122" stroke-width="1.5"/><path d="M4,7 L6.3,9.2 L12.5,2.6" fill="none" stroke="#f37122" stroke-width="1.6"/></svg>Factory recommended service/maintenance</li>
      <li class="services__item"><svg width="14" height="14" viewBox="0 0 14 14"><circle cx="7" cy="7" r="5.8" fill="none" stroke="#f37122" stroke-width="1.5"/><path d="M4,7 L6.3,9.2 L12.5,2.6" fill="none" stroke="#f37122" stroke-width="1.6"/></svg>Oil change</li>
      <li class="services__item"><svg width="14" height="14" viewBox="0 0 14 14"><circle cx="7" cy="7" r="5.8" fill="none" stroke="#f37122" stroke-width="1.5"/><path d="M4,7 L6.3,9.2 L12.5,2.6" fill="none" stroke="#f37122" stroke-width="1.6"/></svg>Fuel system repair and maintenance</li>
      <li class="services__item"><svg width="14" height="14" viewBox="0 0 14 14"><circle cx="7" cy="7" r="5.8" fill="none" stroke="#f37122" stroke-width="1.5"/><path d="M4,7 L6.3,9.2 L12.5,2.6" fill="none" stroke="#f37122" stroke-width="1.6"/></svg>Battery system diagnosis &amp; repair</li>
      <li class="services__item"><svg width="14" height="14" viewBox="0 0 14 14"><circle cx="7" cy="7" r="5.8" fill="none" stroke="#f37122" stroke-width="1.5"/><path d="M4,7 L6.3,9.2 L12.5,2.6" fill="none" stroke="#f37122" stroke-width="1.6"/></svg>Check engine light</li>
      <li class="services__item"><svg width="14" height="14" viewBox="0 0 14 14"><circle cx="7" cy="7" r="5.8" fill="none" stroke="#f37122" stroke-width="1.5"/><path d="M4,7 L6.3,9.2 L12.5,2.6" fill="none" stroke="#f37122" stroke-width="1.6"/></svg>Electrical problems</li>
      <li class="services__item"><svg width="14" height="14" viewBox="0 0 14 14"><circle cx="7" cy="7" r="5.8" fill="none" stroke="#f37122" stroke-width="1.5"/><path d="M4,7 L6.3,9.2 L12.5,2.6" fill="none" stroke="#f37122" stroke-width="1.6"/></svg>Engine performance</li>
      <li class="services__item"><svg width="14" height="14" viewBox="0 0 14 14"><circle cx="7" cy="7" r="5.8" fill="none" stroke="#f37122" stroke-width="1.5"/><path d="M4,7 L6.3,9.2 L12.5,2.6" fill="none" stroke="#f37122" stroke-width="1.6"/></svg>Exhaust problems</li>
      <li class="services__item"><svg width="14" height="14" viewBox="0 0 14 14"><circle cx="7" cy="7" r="5.8" fill="none" stroke="#f37122" stroke-width="1.5"/><path d="M4,7 L6.3,9.2 L12.5,2.6" fill="none" stroke="#f37122" stroke-width="1.6"/></svg>Tires</li>
      <li class="services__item"><svg width="14" height="14" viewBox="0 0 14 14"><circle cx="7" cy="7" r="5.8" fill="none" stroke="#f37122" stroke-width="1.5"/><path d="M4,7 L6.3,9.2 L12.5,2.6" fill="none" stroke="#f37122" stroke-width="1.6"/></svg>30/60/90 K mileage maintenance services</li>
      <li class="services__item"><svg width="14" height="14" viewBox="0 0 14 14"><circle cx="7" cy="7" r="5.8" fill="none" stroke="#f37122" stroke-width="1.5"/><path d="M4,7 L6.3,9.2 L12.5,2.6" fill="none" stroke="#f37122" stroke-width="1.6"/></svg>Cooling system repair and maintenance</li>
      <li class="services__item"><svg width="14" height="14" viewBox="0 0 14 14"><circle cx="7" cy="7" r="5.8" fill="none" stroke="#f37122" stroke-width="1.5"/><path d="M4,7 L6.3,9.2 L12.5,2.6" fill="none" stroke="#f37122" stroke-width="1.6"/></svg>Air conditioning / heating repair</li>
      <li class="services__item"><svg width="14" height="14" viewBox="0 0 14 14"><circle cx="7" cy="7" r="5.8" fill="none" stroke="#f37122" stroke-width="1.5"/><path d="M4,7 L6.3,9.2 L12.5,2.6" fill="none" stroke="#f37122" stroke-width="1.6"/></svg>Brake system</li>
      <li class="services__item"><svg width="14" height="14" viewBox="0 0 14 14"><circle cx="7" cy="7" r="5.8" fill="none" stroke="#f37122" stroke-width="1.5"/><path d="M4,7 L6.3,9.2 L12.5,2.6" fill="none" stroke="#f37122" stroke-width="1.6"/></svg>Steering &amp; suspension</li>
    </ul>
  </section>

  <p class="about">Quarrytide Production Services Ltd. has set up and successfully operates a complete equipment repair facility. First set up to be a dedicated repair shop for a single large client, Quarrytide has now expanded to include all manner of clients with diverse equipment needs. With Journeyman and Apprentice HD mechanics available 24 hours a day our facility is ready to handle all of your equipment needs. We are an ‘approved’ repair facility for a growing list of equipment manufacturers including: Tarnvale, Corbrook, Liftwell, Hartmoor, Ridgecrane etc.</p>

  <div class="photo photo--round photo--oil" role="img" aria-label="Photo of golden motor oil being poured into an engine"></div>

  <p class="website">www.quarrytide.net</p>

  <div class="contact">
    <p class="contact__label">Call us for more information</p>
    <p class="contact__phone"><svg width="28" height="40" viewBox="0 0 28 40" aria-hidden="true"><path d="M8,2 L13,10 L9,14 C10,20 13,25 17,28 L21,25 L27,32 L22,38 C12,36 2,22 3,8 Z" fill="var(--white)"/></svg>780 555 0172</p>
  </div>
</main>
</body>
</html>
```